Zeltrova - Clever Automation

We are a software house for Audio Visual Systems integration/automation and home automation. we develop innovative software to automate a variety of devices mainly related to audio visuals and we design touch panel user interfaces to control these systems.

We would like to see designs that stick to our colours and theme, which you can find on our webpage www.zeltrova.com.au

The final design should communicate touch panels, innovation, software and automation.

Industry/Entity Type

Software

Requirements
Must have
• The business card must show the following information:
Name example : Derek Thalwin
Qualification example: B Eng ICT(CompSys) Dip EngPrac
Title example : Control Systems Programmer
Mobile Phone, Company phone, Email address ,Company website

```html
<!DOCTYPE html>
<html lang="en">
<head>
<meta charset="utf-8">
<title>Zeltrova – Business Card</title>
<link href="https://fonts.googleapis.com/css2?family=Poppins:wght@400;500;600&display=swap" rel="stylesheet">
<style>
  :root {
    --brand-blue: #1f6fb8;
    --brand-green: #1f9e5a;
    --text-grey: #555a60;
    --card-white: #ffffff;
    --backdrop: #e4e6e9;
  }
  * { margin: 0; padding: 0; box-sizing: border-box; }
  html, body {
    width: 1200px; height: 750px; overflow: hidden;
    background: var(--backdrop);
    font-family: "Poppins", sans-serif;
  }
  .stage { position: relative; width: 1200px; height: 750px; }
  .card {
    position: absolute;
    background: var(--card-white);
    border-radius: 10px;
    box-shadow: 0 2px 8px rgba(0,0,0,0.12);
    overflow: hidden;
  }
  .card--front { left: 77px; top: 117px; width: 510px; height: 292px; }
  .card--back { left: 613px; top: 325px; width: 511px; height: 291px; }

  .edge-bar { position: absolute; top: 131px; width: 11px; height: 128px; }
  .edge-bar--green { left: 0; background: var(--brand-green); border-radius: 0 4px 4px 0; }
  .edge-bar--blue { right: 0; background: var(--brand-blue); border-radius: 4px 0 0 4px; }

  .brand { position: absolute; display: flex; align-items: center; }
  .brand__mark { background: var(--brand-blue); border-radius: 6px; }
  .brand__name {
    color: var(--brand-green);
    font-weight: 500;
    letter-spacing: 0.2px;
    line-height: 1;
  }
  .card--front .brand { right: 18px; top: 16px; gap: 10px; }
  .card--front .brand__mark { width: 52px; height: 52px; }
  .card--front .brand__name { font-size: 29px; }
  .card--back .brand { left: 128px; top: 110px; gap: 12px; }
  .card--back .brand__mark { width: 68px; height: 68px; border-radius: 8px; }
  .card--back .brand__name { font-size: 38px; }

  .person { position: absolute; left: 83px; top: 112px; }
  .person__name { color: var(--brand-blue); font-size: 19px; font-weight: 600; line-height: 1.2; letter-spacing: -0.2px; }
  .person__title { color: var(--text-grey); font-size: 12.5px; line-height: 1.4; }

  .contacts { position: absolute; left: 80px; top: 180px; list-style: none; }
  .contacts li {
    display: flex; align-items: center; gap: 7px;
    color: var(--text-grey); font-size: 12.5px; line-height: 16.6px;
  }
  .contacts svg { width: 12px; height: 12px; flex: none; }

  .back-url {
    position: absolute; left: 0; right: 0; bottom: 10px;
    text-align: center; color: var(--brand-blue); font-size: 13px;
  }
</style>
</head>
<body>
<main class="stage">
  <section class="card card--front" aria-label="Business card front">
    <span class="edge-bar edge-bar--green"></span>
    <span class="edge-bar edge-bar--blue"></span>

    <div class="brand">
      <span class="brand__mark"></span>
      <span class="brand__name">zeltrova</span>
    </div>

    <div class="person">
      <h1 class="person__name">Derek Thalwin</h1>
      <p class="person__title">Control Systems Programmer</p>
    </div>

    <ul class="contacts">
      <li>
        <svg viewBox="0 0 12 12" aria-hidden="true"><rect x="2.5" y="0.5" width="7" height="11" rx="1.5" fill="var(--brand-blue)"/><rect x="3.8" y="2" width="4.4" height="6.5" fill="#fff"/><circle cx="6" cy="9.9" r="0.7" fill="#fff"/></svg>
        0412 587 903
      </li>
      <li>
        <svg viewBox="0 0 12 12" aria-hidden="true"><circle cx="6" cy="6" r="6" fill="var(--brand-blue)"/><path d="M3.6 3.2l1.3-.4.8 1.6-.8.6c.4.9 1 1.5 1.9 1.9l.6-.8 1.6.8-.4 1.3c-2.6-.2-4.8-2.4-5-5z" fill="#fff"/></svg>
        0298 360 451
      </li>
      <li>
        <svg viewBox="0 0 12 12" aria-hidden="true"><rect x="0.5" y="2" width="11" height="8" rx="2" fill="var(--brand-blue)"/><rect x="2" y="3.6" width="8" height="4.8" rx="1" fill="#fff"/></svg>
        dthalwin@zeltrova.com.au
      </li>
      <li>
        <svg viewBox="0 0 12 12" aria-hidden="true"><circle cx="6" cy="6" r="5.5" fill="var(--brand-blue)"/><g fill="none" stroke="#fff" stroke-width="0.8"><ellipse cx="6" cy="6" rx="2.2" ry="5"/><path d="M1 6h10M1.8 3.5h8.4M1.8 8.5h8.4"/></g></svg>
        www.zeltrova.com.au
      </li>
    </ul>
  </section>

  <section class="card card--back" aria-label="Business card back">
    <div class="brand">
      <span class="brand__mark"></span>
      <span class="brand__name">zeltrova</span>
    </div>
    <p class="back-url">www.zeltrova.com.au</p>
  </section>
</main>
</body>
</html>
```